Stationery Set for Velmora Company

I need to create full stationery design for my company; Business Cards, Envelops, Letter Heads, Calendar.
In the letter head and Envelops... only contact information and website links.
Our company is a Service Management company with different domains of innovative services including Technology Service Management, Education Services, Outsourcing Management, Events Management.
I need a modern and innovative design specially for the business card. I some transparent designs and I like it, but don't limit your innovation to what I mentioned. Sky is limit for your innovation.

Target Market(s)

Middle East & Africa

Industry/Entity Type

Business Management

Colors
34a7d8
0355a3
85acd3
86cae7
cee9f5
cfdeed
e4daeb
f3f1f8
ecf7fb

Requirements
Must have
• Name, Title, Email, Mobile
Nice to have
• We have multiple locations in USA, KSA, EGY, so I need ideas about how to include all contact details maybe QR / Barcode or something else.
• Please see our locations and contact information: www.brightvelmora.example
Should not have
• Too much text

```html
<!DOCTYPE html>
<html lang="en">
<head>
<meta charset="utf-8">
<title>Velmora Company – Envelope</title>
<link href="https://fonts.googleapis.com/css2?family=Quicksand:wght@500;700&display=swap" rel="stylesheet">
<style>
  :root {
    --page: #ffffff;
    --silver-dark: #c9c6c3;
    --silver-mid: #dcdad8;
    --silver-light: #f1f0ef;
    --mark-grey: #8c8c8c;
    --address-blue: #1f9bd8;
    --band: #eeeeee;
    --window: #ffffff;
    --edge: #9a9a9a;
  }
  html, body {
    margin: 0;
    width: 1200px;
    height: 1000px;
    overflow: hidden;
    background: var(--page);
  }
  .canvas {
    position: relative;
    width: 1200px;
    height: 1000px;
  }
  .envelope {
    position: absolute;
    left: 20px;
    top: 210px;
    width: 1160px;
    height: 580px;
    overflow: hidden;
    background:
      linear-gradient(90deg,
        var(--silver-dark) 0%,
        var(--silver-mid) 12%,
        var(--silver-dark) 22%,
        var(--silver-light) 30%,
        var(--silver-mid) 38%,
        var(--silver-dark) 52%,
        var(--silver-mid) 62%,
        var(--silver-light) 76%,
        var(--silver-mid) 86%,
        var(--silver-dark) 100%);
    box-shadow: 0 2px 6px rgba(0,0,0,0.25);
  }
  .envelope__sheen {
    position: absolute;
    inset: 0;
    background: linear-gradient(180deg, rgba(255,255,255,0.15) 0%, rgba(255,255,255,0) 40%, rgba(255,255,255,0.12) 100%);
  }
  .envelope__flourish {
    position: absolute;
    left: 0;
    top: 0;
    width: 500px;
    height: 400px;
    background: radial-gradient(ellipse at 10% 35%, rgba(255,255,255,0.35), rgba(255,255,255,0) 65%);
  }
  .brand {
    position: absolute;
    left: 75px;
    top: 86px;
    display: flex;
    align-items: center;
    gap: 12px;
    color: var(--mark-grey);
  }
  .brand__dot {
    width: 14px;
    height: 14px;
    border-radius: 50%;
    background: var(--mark-grey);
  }
  .brand__name {
    font-family: "Quicksand", sans-serif;
    font-weight: 700;
    font-size: 60px;
    line-height: 1;
    letter-spacing: 1px;
  }
  .return-address {
    position: absolute;
    left: 74px;
    top: 213px;
    margin: 0;
    font-family: "Quicksand", sans-serif;
    font-weight: 500;
    font-size: 19px;
    line-height: 29px;
    color: var(--address-blue);
    font-style: normal;
  }
  .band {
    position: absolute;
    left: 10px;
    top: 455px;
    width: 1160px;
    height: 44px;
    background: linear-gradient(90deg, var(--band), #ffffff 30%, #e2e2e2 55%, #f5f5f5 80%, var(--band));
    border-top: 1px solid var(--edge);
    border-bottom: 1px solid var(--edge);
  }
  .address-window {
    position: absolute;
    left: 642px;
    top: 332px;
    width: 476px;
    height: 200px;
    background: var(--window);
    border: 1px solid var(--edge);
    border-radius: 14px;
  }
</style>
</head>
<body>
  <div class="canvas">
    <div class="envelope">
      <div class="envelope__sheen"></div>
      <div class="envelope__flourish" role="img" aria-label="Soft silver wave-line decoration in the top left corner"></div>

      <div class="brand">
        <div class="brand__name">Velmora</div>
        <div class="brand__dot"></div>
      </div>

      <address class="return-address">
        418 Harbor Crest Lane, 5th<br>
        Floor Bayhaven CA 90412<br>
        US
      </address>

      <div class="band"></div>
      <div class="address-window"></div>
    </div>
  </div>
</body>
</html>
```